New stationary design for online film company

We need some new stationary to fit with our new logo. The stationary should be professional, clean and simple.
We need designs for a full set of business stationary.
We need - letterhead, envelopes, invoices, proposals, coverslip/note and cover page

Industry/Entity Type

Business

```html
<!DOCTYPE html>
<html lang="en">
<head>
<meta charset="utf-8">
<title>Streamvale Stationery Set</title>
<link href="https://fonts.googleapis.com/css2?family=Open+Sans:wght@400;600&display=swap" rel="stylesheet">
<style>
  :root {
    --navy: #0e4a73;
    --sky: #6fa3c0;
    --paper: #ffffff;
    --paper-shade: #f1f2f4;
    --ink: #4a4f57;
    --ghost: #e3e4ea;
    --backdrop: #c98b5c;
    --label: #ffffff;
  }
  * { margin: 0; padding: 0; box-sizing: border-box; }
  html, body { width: 1200px; height: 489px; overflow: hidden; }
  body {
    background: var(--backdrop);
    font-family: "Open Sans", Arial, sans-serif;
    color: var(--ink);
    position: relative;
  }
  .sheet, .envelope, .card {
    position: absolute;
    background: linear-gradient(160deg, var(--paper) 40%, var(--paper-shade));
    overflow: hidden;
  }
  .brand-name {
    font-family: "Open Sans", Arial, sans-serif;
    font-weight: 600;
    color: var(--navy);
    letter-spacing: -0.5px;
    white-space: nowrap;
  }
  .brand-dot {
    display: inline-block;
    border-radius: 50%;
    background: var(--navy);
    vertical-align: middle;
  }
  .brand { display: flex; align-items: center; gap: 5px; position: absolute; }
  .wave { position: absolute; left: 0; bottom: 0; width: 100%; }
  .option-label {
    position: absolute; top: 462px; font-size: 24px; color: var(--label);
    transform: translateX(-50%);
  }

  /* Letterhead option 1 */
  .letterhead-one { left: 6px; top: 19px; width: 333px; height: 431px; }
  .letterhead-one .brand { left: 50%; top: 12px; transform: translateX(-50%); }
  .letterhead-one .brand-name { font-size: 22px; }
  .letterhead-one .brand-dot { width: 18px; height: 18px; }
  .backdrop-ring {
    position: absolute; left: -7px; top: 261px; width: 208px; height: 208px;
    border: 22px solid var(--ghost); border-radius: 50%;
  }
  .letterhead-one .footer-line {
    position: absolute; bottom: 9px; left: 0; width: 100%;
    text-align: center; font-size: 5.5px; color: var(--ink);
  }

  /* Letterhead option 2 */
  .letterhead-two { left: 372px; top: 19px; width: 333px; height: 431px; }
  .letterhead-two .brand { left: 15px; top: 12px; }
  .letterhead-two .brand-name { font-size: 22px; }
  .letterhead-two .brand-dot { width: 18px; height: 18px; }
  .contact-block {
    position: absolute; left: 256px; top: 18px; padding-left: 4px;
    border-left: 0.6px solid #c9ccd2; font-size: 5.2px; line-height: 7.6px;
  }
  .letterhead-two .wave { height: 40px; }
  .letterhead-two .address {
    position: absolute; left: 23px; bottom: 8px; font-size: 5.2px; line-height: 7px;
    color: var(--paper);
  }

  /* Envelopes */
  .envelope-back { left: 806px; top: 6px; width: 386px; height: 165px; }
  .envelope-back .flap { position: absolute; left: 0; top: 0; width: 100%; height: 72px; }
  .envelope-back .flap-ring {
    position: absolute; left: 50%; top: 24px; width: 32px; height: 32px; margin-left: -16px;
    border: 4px solid var(--paper); border-radius: 50%;
  }
  .envelope-mid { left: 739px; top: 77px; width: 372px; height: 165px; border: 0.8px solid #2b2b2b; }
  .envelope-mid .flap { position: absolute; left: 0; top: 0; width: 100%; height: 70px; }
  .envelope-mid .flap-ring {
    position: absolute; left: 50%; top: 30px; width: 32px; height: 32px; margin-left: -16px;
    border: 4px solid var(--navy); border-radius: 50%;
  }
  .envelope-front { left: 778px; top: 151px; width: 373px; height: 166px; border: 0.6px solid #d8d8d8; }
  .envelope-front .brand { left: 12px; top: 18px; }
  .envelope-front .brand-name { font-size: 20px; }
  .envelope-front .brand-dot { width: 16px; height: 16px; }
  .envelope-front .address { position: absolute; left: 36px; top: 44px; font-size: 5.2px; }
  .envelope-front .wave { height: 38px; }
  .envelope-front .web {
    position: absolute; left: 48px; bottom: 9px; font-size: 6.5px; letter-spacing: 1.6px; color: var(--paper);
  }

  /* Business cards */
  .card { top: 346px; width: 186px; height: 105px; border: 0.6px solid #d8d8d8; }
  .card-front { left: 770px; }
  .card-front .brand { left: 50%; top: 7px; transform: translateX(-50%); }
  .card-front .brand-name { font-size: 17px; }
  .card-front .brand-dot { width: 13px; height: 13px; }
  .card-front .card-address {
    position: absolute; right: 96px; top: 52px; text-align: right; font-size: 4.6px; line-height: 6.8px;
  }
  .card-front .card-contacts {
    position: absolute; left: 93px; top: 50px; padding-left: 4px; border-left: 0.5px solid #c9ccd2;
    font-size: 4.6px; line-height: 6.8px;
  }
  .card-front .wave { height: 30px; }
  .card-front .holder {
    position: absolute; left: 30px; bottom: 5px; text-align: center; color: var(--paper);
  }
  .card-front .holder-name { font-size: 6.3px; font-weight: 600; }
  .card-front .holder-title { font-size: 4.3px; }
  .card-back { left: 972px; }
  .card-back .back-ring {
    position: absolute; left: 50%; top: 22px; width: 50px; height: 50px; margin-left: -25px;
    border: 7px solid var(--navy); border-radius: 50%;
  }
  .card-back .web {
    position: absolute; left: 0; width: 100%; bottom: 12px; text-align: center;
    font-size: 6px; letter-spacing: 1.3px; color: var(--ink);
  }
</style>
</head>
<body>

  <section class="sheet letterhead-one">
    <div class="backdrop-ring"></div>
    <div class="brand"><span class="brand-dot"></span><span class="brand-name">streamvale</span></div>
    <p class="footer-line">Street Name, City Name, State Zip Code &nbsp;|&nbsp; ✆ 555-201-4730 &nbsp; ✉ hello@streamvale.com &nbsp; ◍ www.streamvale.com</p>
  </section>
  <span class="option-label" style="left:164px">Option-1</span>

  <section class="sheet letterhead-two">
    <div class="brand"><span class="brand-dot"></span><span class="brand-name">streamvale</span></div>
    <div class="contact-block">✆ 555-201-4730<br>✉ hello@streamvale.com<br>◍ www.streamvale.com</div>
    <svg class="wave" viewBox="0 0 333 40" preserveAspectRatio="none" aria-hidden="true">
      <path d="M0 24 C90 0 170 2 240 20 C280 30 310 26 333 14 L333 40 L0 40 Z" fill="var(--navy)"/>
      <path d="M0 22 C90 -2 170 0 240 17 C280 26 310 22 333 10" fill="none" stroke="var(--sky)" stroke-width="2.5"/>
      <path d="M0 19 C90 -5 170 -3 240 13 C280 22 310 18 333 6" fill="none" stroke="var(--sky)" stroke-width="0.8"/>
    </svg>
    <p class="address">Street Name, City Name<br>State Zip Code</p>
  </section>
  <span class="option-label" style="left:538px">Option-2</span>

  <section class="envelope envelope-back">
    <svg class="flap" viewBox="0 0 386 72" preserveAspectRatio="none" aria-hidden="true">
      <path d="M0 0 H386 V8 C386 20 370 26 340 34 L220 66 C205 71 181 71 166 66 L46 34 C16 26 0 20 0 8 Z" fill="var(--navy)"/>
    </svg>
    <div class="flap-ring"></div>
  </section>

  <section class="envelope envelope-mid">
    <svg class="flap" viewBox="0 0 372 70" preserveAspectRatio="none" aria-hidden="true">
      <path d="M0 0 C6 12 12 22 34 28 L172 66 C180 68 192 68 200 66 L338 28 C360 22 366 12 372 0" fill="none" stroke="#2b2b2b" stroke-width="1"/>
    </svg>
    <div class="flap-ring"></div>
  </section>

  <section class="envelope envelope-front">
    <div class="brand"><span class="brand-dot"></span><span class="brand-name">streamvale</span></div>
    <p class="address">Street Name, City Name, State Zip Code</p>
    <svg class="wave" viewBox="0 0 373 38" preserveAspectRatio="none" aria-hidden="true">
      <path d="M0 24 C90 4 170 4 250 22 C300 32 340 28 373 12 L373 38 L0 38 Z" fill="var(--navy)"/>
      <path d="M0 21 C90 1 170 1 250 19 C300 28 340 24 373 9" fill="none" stroke="var(--sky)" stroke-width="2.5"/>
      <path d="M0 18 C90 -2 170 -2 250 15 C300 24 340 20 373 5" fill="none" stroke="var(--sky)" stroke-width="0.8"/>
    </svg>
    <p class="web">www.streamvale.com</p>
  </section>

  <section class="card card-front">
    <div class="brand"><span class="brand-dot"></span><span class="brand-name">streamvale</span></div>
    <p class="card-address">Street Name<br>City Name<br>State Zip Code</p>
    <p class="card-contacts">✆ 555-201-4730<br>☏ 555-201-4731<br>✉ hello@streamvale.com<br>◍ www.streamvale.com</p>
    <svg class="wave" viewBox="0 0 186 30" preserveAspectRatio="none" aria-hidden="true">
      <path d="M0 16 C50 2 95 4 130 16 C155 24 172 20 186 10 L186 30 L0 30 Z" fill="var(--navy)"/>
      <path d="M0 14 C50 0 95 2 130 13 C155 21 172 17 186 7" fill="none" stroke="var(--sky)" stroke-width="1.8"/>
    </svg>
    <div class="holder"><p class="holder-name">Your Name</p><p class="holder-title">Title</p></div>
  </section>

  <section class="card card-back">
    <div class="back-ring"></div>
    <p class="web">www.streamvale.com</p>
  </section>

</body>
</html>
```